Corporate Design für Lunavello - innovatives Unternehmen im Bereich App-Entwicklung und Kultur
Zielgruppe
Gegenstand des Unternehmens ist:
- Entwurf, Entwicklung und Vermarktung von Soziale Netzwerk-Apps für Unternehmen im Kultursektor und für einzelne Kunstprojekte
- Beratung von Kultureinrichtungen
- Technische Umsetzung als Dienstleister von digitalen Apps, Websites, Softwares für den Kulturbereich
- Entwicklung und Erstellung von digitalen Diensten im Kulturbereich
- Entwicklung von Augmented Reality und 3D Technologien für mobile Devices
- Ausbildung im Bereich Kultur und Kreativität
- Erbringung von Dienstleistungen im Media- und Marketingbereich
- Organisation von Kulturveranstaltungen
Zielgruppe sind insbesondere Kreative und Kultureinrichtungen.
www.lunavello.eu
Aufgabenstellung
bitte die Farbe der Website NICHT berücksichtigen. Wir wollen sowieso die Website ändern.
bitte keine Fernseher, Kameras, Videokameras im Logo. Wir bevorzugen etwas abstraktes.
Danke und viel Spass!!

```html
<!DOCTYPE html>
<html lang="de">
<head>
<meta charset="utf-8">
<title>Lunavello – Visitenkarte</title>
<link rel="stylesheet" href="https://fonts.googleapis.com/css2?family=Exo+2:wght@300;400;500&display=swap">
<style>
  :root {
    --paper: #ececec;
    --card: #474747;
    --ink: #ffffff;
    --ink-soft: #e2e2e2;
    --accent: #f5ab2e;
  }
  * { box-sizing: border-box; margin: 0; padding: 0; }
  html, body {
    width: 1200px;
    height: 1142px;
    overflow: hidden;
    background: var(--paper);
    font-family: "Exo 2", "Segoe UI", sans-serif;
  }
  .sheet {
    position: relative;
    width: 1200px;
    height: 1142px;
  }
  .card {
    position: absolute;
    left: 340px;
    width: 520px;
    height: 320px;
    background: var(--card);
    color: var(--ink);
  }
  .card--front { top: 200px; }
  .card--back  { top: 610px; }

  .brand {
    position: absolute;
    inset: 0;
    display: flex;
    align-items: center;
    justify-content: center;
    gap: 16px;
  }
  .brand__dot {
    width: 30px;
    height: 30px;
    border-radius: 50%;
    background: var(--accent);
  }
  .brand__name {
    font-size: 44px;
    font-weight: 400;
    letter-spacing: 1px;
    color: var(--ink);
  }

  .contact {
    position: absolute;
    left: 0;
    right: 0;
    top: 74px;
    text-align: center;
  }
  .contact__name {
    font-size: 27px;
    font-weight: 500;
    letter-spacing: 1px;
  }
  .contact__role {
    margin-top: 2px;
    font-size: 13px;
    font-weight: 300;
    color: var(--ink-soft);
    letter-spacing: 0.5px;
  }
  .contact__list {
    display: grid;
    grid-template-columns: 90px auto;
    column-gap: 14px;
    row-gap: 2px;
    width: max-content;
    margin: 20px auto 0 auto;
    font-size: 14px;
    letter-spacing: 1px;
    text-align: left;
  }
  .contact__label {
    text-align: right;
    font-weight: 300;
    color: var(--ink-soft);
  }
  .contact__value { font-weight: 400; }
</style>
</head>
<body>
  <main class="sheet">
    <section class="card card--front" aria-label="Vorderseite">
      <div class="brand">
        <span class="brand__dot"></span>
        <span class="brand__name">lunavello</span>
      </div>
    </section>

    <section class="card card--back" aria-label="Rückseite">
      <div class="contact">
        <h1 class="contact__name">Lena Falkner</h1>
        <p class="contact__role">Geschäftsführerin</p>
        <dl class="contact__list">
          <dt class="contact__label">Mobil:</dt>
          <dd class="contact__value">04821/3069274</dd>
          <dt class="contact__label">Fax:</dt>
          <dd class="contact__value">04821/3069275</dd>
          <dt class="contact__label">E-Mail:</dt>
          <dd class="contact__value">l.falkner@lunavello.eu</dd>
        </dl>
      </div>
    </section>
  </main>
</body>
</html>
```